Business Card Design

I already have a company logo for my company. I have a logo for the manufacturer we represent. I want a professional business card design.

```html
<!DOCTYPE html>
<html lang="en">
<head>
<meta charset="utf-8">
<title>Beacon Guard LLC – Business Card</title>
<link href="https://fonts.googleapis.com/css2?family=Open+Sans:wght@400;600;700&display=swap" rel="stylesheet">
<style>
  :root {
    --stage: #2b2e33;
    --card-white: #ffffff;
    --card-black: #121212;
    --brand-red: #e11f26;
    --brand-gold: #e0a516;
    --ink: #2a2a2a;
    --ink-soft: #555555;
  }
  * { margin: 0; padding: 0; box-sizing: border-box; }
  html, body {
    width: 1200px; height: 900px; overflow: hidden;
    background: var(--stage);
    font-family: "Open Sans", Arial, sans-serif;
  }
  .stage {
    position: relative; width: 1200px; height: 900px;
    display: flex; flex-direction: column; align-items: center; justify-content: center; gap: 52px;
  }
  .card {
    position: relative; width: 620px; height: 354px;
    border-radius: 22px; overflow: hidden;
    box-shadow: 0 12px 30px rgba(0,0,0,.45);
  }
  .card-front { background: var(--card-white); }
  .card-back { background: var(--card-black); display: flex; align-items: center; justify-content: center; }
  .front-shapes { position: absolute; inset: 0; }
  .brand-mark { display: flex; align-items: center; gap: 12px; }
  .brand-mark .brand-square { width: 22px; height: 22px; background: var(--brand-red); }
  .brand-mark .brand-name {
    font-weight: 700; font-size: 34px; letter-spacing: 1px; color: var(--brand-red);
    text-transform: uppercase; line-height: 1;
  }
  .card-back .brand-name { color: #ffffff; font-size: 44px; }
  .card-front .brand-mark { position: absolute; left: 250px; top: 62px; }
  .person { position: absolute; left: 172px; top: 190px; text-align: right; width: 150px; }
  .person-name { color: var(--brand-red); font-weight: 600; font-size: 22px; line-height: 1.15; }
  .person-title { color: var(--ink); font-size: 13px; margin-top: 3px; }
  .divider { position: absolute; left: 336px; top: 192px; width: 2px; height: 64px; background: var(--brand-gold); }
  .contact { position: absolute; left: 352px; top: 190px; list-style: none; }
  .contact li { display: flex; align-items: center; gap: 8px; font-size: 14px; color: var(--ink); line-height: 22px; }
  .contact svg { width: 12px; height: 12px; fill: var(--brand-red); flex: none; }
</style>
</head>
<body>
<main class="stage">
  <section class="card card-front" aria-label="Card front">
    <svg class="front-shapes" viewBox="0 0 620 354" preserveAspectRatio="none">
      <path d="M0 0 H70 C130 70 40 170 110 240 C160 290 130 330 150 354 H0 Z" fill="var(--card-black)"/>
      <path d="M70 0 C130 70 40 170 110 240 C160 290 130 330 150 354" fill="none" stroke="var(--brand-gold)" stroke-width="4"/>
      <path d="M620 238 C500 300 360 318 232 354 H620 Z" fill="var(--brand-red)"/>
      <path d="M620 226 C500 290 360 312 220 354" fill="none" stroke="var(--brand-gold)" stroke-width="2"/>
    </svg>
    <div class="brand-mark">
      <span class="brand-square"></span>
      <span class="brand-name">Beacon Guard LLC</span>
    </div>
    <div class="person">
      <p class="person-name">Daniel Reed</p>
      <p class="person-title">Managing Director</p>
    </div>
    <span class="divider"></span>
    <ul class="contact">
      <li><svg viewBox="0 0 12 12"><path d="M2 1h3l1 3-1.5 1a7 7 0 0 0 2.5 2.5L8 6l3 1v3c0 .6-.4 1-1 1A9 9 0 0 1 1 2c0-.6.4-1 1-1z"/></svg>555.210.0147</li>
      <li><svg viewBox="0 0 12 12"><path d="M1 2h10v8H1z M1 2l5 4 5-4" stroke="#fff" stroke-width=".8"/></svg>info@beaconguardllc.com</li>
      <li><svg viewBox="0 0 12 12"><circle cx="6" cy="6" r="5"/></svg>www.beaconguardllc.com</li>
    </ul>
  </section>

  <section class="card card-back" aria-label="Card back">
    <div class="brand-mark">
      <span class="brand-square"></span>
      <span class="brand-name">Beacon Guard LLC</span>
    </div>
  </section>
</main>
</body>
</html>
```